Field Basket - Store need a label design

We need a Label Design for our Cosmetic Line with Hemp Cosmetics. We do not want a hemp leaf on our design. We want our LOGO infront of the design with the name of the product (shower gel, body lotion, .....) The ingredients must be included as well as in the bottle within 12 months. The font is smaller than 3mm. Generally, the font must be at least 2mm in size. What we need: 100x140mm 200ml E 12m 4x as: Hemp - shampoo, shower gel, body lotion and hair balm 20x66 mm 50g E (2 pieces for front and back) as: face cream, hand cream 42x52mm as: lip balm (sample how it should look in the uploaded files with the name morvil) What else should be on it: WITHOUT artificial colors and fragrances WITHOUT paraffins WITHOUT silicones with pure hemp seed oil Product not tested on animals Manufacturer: MORVIL A-4812 GRUNDLACH Description: HANF-SHAMPOO 200 ml Skin-mild washing-active ingredients develop a particularly pleasant and gentle cleansing effect. High-quality hemp seed oil nourishes the hair in a natural way and makes it pleasantly soft, loose and supple. BRISK MEADOW- is suitable for all hair types, especially for damaged and dull hair. HEMP SHOWER BATH 200 ml The pleasant foam cleans mildly and gently. The excellent care effect of natural hemp seed oil makes skin and hair pleasantly soft and supple.BRISK MEADOW- is suitable for mild cleansing and care, especially of sensitive skin and damaged hair. HEMP-FOAM BATH 200 ml Skin-mild washing-active ingredients develop a particularly mild and creamy foam. The excellent care effect of natural hemp seed oil makes the skin exceptionally soft and supple.BRISK MEADOW- is suitable for mild cleansing and care, especially of sensitive, rough and chapped skin. HEMP HAIR BALM 200 ml A special combination of natural hemp seed oil and other high-quality vegetable oils cares for the hair perfectly and makes it pleasantly soft, loose, supple, naturally shiny, extremely easy to style and effectively prevents the cleavage of the tips. BRISK MEADOW HEMP HAIR BALM is suitable for all hair types, especially for damaged, damaged, brittle and dull hair, as well as split hair tips. HEMP BODY LOTION 200 ml Pure Hemp Seed Oil nourishes the skin naturally, prevents it from drying out too much and makes it particularly soft and supple.BRISK MEADOW HEMP BODY LOTION is for pleasant body care, especially after bathing, especially in dry, brittle and sensitive skin HEMP FACE CREAM 50 g The particularly high content of pure hemp seed oil nourishes the skin perfectly and makes it unusually soft and supple.BRISK MEADOW HEMP FACE CREAM is suitable for pleasant and moisturizing care of the entire face, especially for dry and brittle skin Skin. HEMP HAND CREAM 50 g The high content of pure hemp seed oil and natural beeswax protects and nourishes the skin perfectly and makes it soft and supple. BRISK MEADOW HEMP HAND CREAM is suitable for protective care especially of stressed, sensitive and brittle skin. HEMP LIP BALM 6 g Natural hemp seed oil, pure beeswax and other valuable ingredients provide long-lasting care for the lips and protect them from adverse weather conditions and dehydration.BRISK MEADOW HEMP LIP BALM is particularly suitable for the lasting care of sensitive, brittle and torn lips. HANF-SHAMPOO Ingredients (INCI): Aqua, Sodium Laureth Sulfate, TEA-Lauryl Sulfate, Disodium Laureth Sulfosuccinate, Potassium Cocoyl Hydrolized Collagen, Linoleamide-DEA, Cannabis Sativa Seed Oil, Natural Perfume, Sodium Chloride, Citric Acid, Potassium Sorbate, Panthenol , Tocopherol, chlorophyll, citral *, citronellol *, geraniol *, limonene *, linalool *. (* natural ingredients of essential oils). HEMP-DUSCHBAD Ingredients (INCI): Aqua, Sodium Laureth Sulfate, TEA-Lauryl Sulfate, Disodium Laureth Sulfosuccinate, Potassium Cocoyl Hydrolized Collagen, Cocoamphodiacetate, Linoleamide-DEA, Cocamidopropylamine Oxide, Cannabis Sativa Seed Oil, Natural Perfume, Coco-Glucoside, Glyceryl Oleate, Sodium Chloride, Citric Acid, Potassium Sorbate, Panthenol, Tocopherol, Chlorophyll, Citral *, Citronellol *, Geraniol *, Limonene *, Linalool *. (* natural ingredients of essential oils). HANF-SCHAUMBAD Ingredients (INCI): Aqua, MIPA-Pareth-25-Sulfate, Cocamidopropyl Betaine, Disodium Laureth Sulfosuccinate, Linoleamide-DEA, Cannabis Sativa Seed Oil, Coco-Glucoside, Glyceryl Oleate, Natural Perfume, Panthenol, Potassium Sorbate, Citric Acid, tocopherol, chlorophyll, citral *, citronellol *, geraniol *, limonene *, linalool *. * (* Natural constituents of essential oils). HANF-HAARBALSAM Ingredients (INCI): Aqua, Ceteareth-20, Cetearyl Alcohol, Dicocodimonium Chloride, Glycerine, Cannabis Sativa Seed Oil, Coco-Glucoside, Glyceryl Oleate, Natural Perfume, Potassium Sorbate, Panthenol, Citric Acid, Tocopherol, Chlorophyll, Citral *, Citronellol *, geraniol *, limonene *, linalool *. (* natural ingredients of essential oils). Hemp Facial Ingredients (INCI): Aqua, Cannabis Sativa Seed Oil, Cetearyl Alcohol, Cetearyl Glucoside, Sodium Cetearyl Sulfate, Hexyl Decanol, Glycerine, Natural Perfume, Benzyl Alcohol, Potassium Sorbate, Sodium Benzoate, Tocopherol, Panthenol, Citric Acid, Citral * , Citronellol *, geraniol *, limonene *, linalool *. (* natural ingredients of essential oils). HANF HAND CREAM Ingredients (INCI): Cannabis sativa Seed Oil, Cocos Nucifera Oil, Cera Alba, Tocopherol, Natural Perfume, Citral *, Citronellol *, Geraniol *, Limonene *, Linalool *. (* natural ingredients of essential oils). HEMP BODY LOTION INGREDIENTS (INCI): Aqua, Cannabis Sativa Seed Oil, Cetearyl Alcohol, Ceteareth-12, Cetearyl Glucoside, Glycerol, Hexyldecanol, Natural Perfume, Benzyl Alcohol, Potassium Sorbate, Sodium Benzoate, Tocopherol, Panthenol, Citric Acid, Geraniol , Limonene *, linalool *, citronellol *, citral *, (* natural constituents of essential oils). HEMP LIP BALM Ingredients (INCI): Cannabis sativa Seed Oil, Cocos nucifera Oil, Cera Alba, Natural Perfume, Citral *, Citronellol *, Geraniol *, Limonene *, Linalool *. (* natural ingredients of essential oils).

Colors

Designer to choose colors to be used in the design.

Requirements
Must have
• The Sentence: Natural Spirit - Feel the nature should be in front of the label as our slogan for the Cosmetic Line
Should not have
• Hemp leaf

```html
<!DOCTYPE html>
<html lang="de">
<head>
<meta charset="utf-8">
<title>Hanf Handcreme – Rückseite</title>
<link href="https://fonts.googleapis.com/css2?family=Roboto+Condensed:wght@300;400&family=Caveat+Brush&display=swap" rel="stylesheet">
<style>
  :root {
    --label-teal: #3fa99b;
    --paper: #ffffff;
    --ink-light: #ffffff;
    --ink-grey: #5a5a5a;
    --rule: #3fa99b;
  }
  html, body {
    margin: 0;
    padding: 0;
    overflow: hidden;
    background: var(--paper);
  }
  .label {
    position: relative;
    width: 1200px;
    height: 367px;
    background: var(--label-teal);
    overflow: hidden;
  }
  .description {
    position: absolute;
    left: 34px;
    top: 14px;
    width: 640px;
    margin: 0;
    font-family: "Roboto Condensed", Arial, sans-serif;
    font-weight: 400;
    font-size: 29px;
    line-height: 37px;
    color: var(--ink-light);
  }
  .claim {
    position: absolute;
    left: 34px;
    top: 206px;
    width: 660px;
    margin: 0;
    font-family: "Caveat Brush", cursive;
    font-size: 34px;
    line-height: 41px;
    color: var(--ink-light);
  }
  .claim .line-brand {
    letter-spacing: 1px;
  }
  .info-panel {
    position: absolute;
    left: 697px;
    top: 19px;
    width: 492px;
    height: 332px;
    background: var(--paper);
  }
  .ingredients {
    position: absolute;
    left: 14px;
    top: 12px;
    width: 470px;
    margin: 0;
    font-family: "Roboto Condensed", Arial, sans-serif;
    font-weight: 400;
    font-size: 19.5px;
    line-height: 34px;
    color: var(--ink-grey);
  }
  .facts {
    position: absolute;
    left: 0;
    top: 262px;
    width: 492px;
    height: 70px;
    border-top: 2px solid var(--rule);
    display: flex;
  }
  .facts .cell {
    display: flex;
    align-items: center;
    justify-content: center;
    font-family: "Roboto Condensed", Arial, sans-serif;
    color: var(--ink-grey);
  }
  .facts .cell + .cell {
    border-left: 2px solid var(--rule);
  }
  .cell-quantity { width: 168px; font-size: 34px; }
  .cell-quantity .unit { font-size: 26px; margin-left: 10px; }
  .cell-estimate { width: 126px; font-size: 40px; font-weight: 300; }
  .cell-shelf { flex: 1; justify-content: flex-start; padding-left: 50px; }
</style>
</head>
<body>
<div class="label">
  <p class="description">
    Der hohe Gehalt an reinem Hanfsamenöl und natürlichem Bienenwachs schützt und pflegt die Haut hervorragend und macht sie weich und geschmeidig.
  </p>

  <p class="claim">
    <span class="line-brand">BRISK MEADOW</span> – eignet sich zur schützenden Pflege besonders von strapazierter, empfindlicher und spröder Haut.
  </p>

  <div class="info-panel">
    <p class="ingredients">
      Ingredients (INCI): Cannabis sativa Seed Oil, Cocos Nucifera Oil, Cera Alba, Tocopherol, Natural Perfume, Citral*, Citronellol*, Geraniol*, Limonene*, Linalool*.<br>
      (* natürliche Bestandteile ätherischer Öle).
    </p>

    <div class="facts">
      <div class="cell cell-quantity">50<span class="unit">mg</span></div>
      <div class="cell cell-estimate">e</div>
      <div class="cell cell-shelf">
        <svg width="40" height="44" viewBox="0 0 40 44" aria-label="Haltbarkeit nach dem Öffnen: 12 Monate">
          <g fill="none" stroke="#333" stroke-width="2">
            <path d="M10 6 L26 2 L28 8 L12 12 Z"/>
            <rect x="6" y="16" width="26" height="22" rx="2"/>
          </g>
          <text x="19" y="33" font-family="Roboto Condensed, Arial, sans-serif" font-size="10" text-anchor="middle" fill="#333">12M</text>
        </svg>
      </div>
    </div>
  </div>
</div>
</body>
</html>
```